New iOS App design for Boston Startup

We are looking for a new app design for our iPhone app. The current app's design feels outdated and we like to add lots of new functionality and a new navigation as well. A complete overhaul therefore!
We want you to design 5 screens that will have changed the most. The complete wireframes of these 5 pages are attached in the requirements document.
Once the winning design is selected we will award the winner with the designing all other screens (40-50 screens based on the same design). This will be a separate project worth $1000. The winning designer can get more follow up work if both sides are happy about the cooperation.
We will give feedback as soon as the first screen has been uploaded for review. Final decision will be made only after all 5 screens are finished.
We hope you give it your best!
Note: will only communicate through PixelHarbor (no skype),
Updates
Reason: Want to give designers a chance to submit their designs as I understand from some, the deadline is too close.
I have raised the award and introduced a 2nd price as well to make it worth your time. I hope you give it your best shot.
Reason: A few of you have asked for an extension of the deadline as time is running out. I will extend by one day. Tell me if you need more.
Industry/Entity Type
Startup
Requirements
Must have
- At least 1 screen before we can give you feedback.
Nice to have
- multiple options of 1 screen to get to a desirable design

```html
<!DOCTYPE html>
<html lang="en">
<head>
<meta charset="utf-8">
<title>Home Screen Options</title>
<link href="https://fonts.googleapis.com/css2?family=Roboto:wght@300;400;500;700&display=swap" rel="stylesheet">
<style>
:root{
  --stage:#b7bdc1;
  --blue:#1ba6d3;
  --blue-deep:#1394c0;
  --ink:#6b6b6b;
  --ink-soft:#8a8a8a;
  --rule:#cfcfcf;
  --paper:#ffffff;
  --ice:#eaf4fb;
  --night:#1c1c1c;
  --night-band:#2a2a2a;
  --night-ink:#bdbdbd;
  --up:#2ecc40;
  --down:#e8463b;
}
*{box-sizing:border-box;margin:0;padding:0}
html,body{width:1200px;height:1000px;overflow:hidden}
body{background:var(--stage);font-family:"Roboto",sans-serif;position:relative}

.screen{position:absolute;width:380px;height:568px;background:var(--paper);overflow:hidden;color:var(--ink);
  --line:var(--rule);--label:var(--ink);--value:var(--ink);--circle:#fff;--circle-edge:#e1e1e1}
.screen--light{left:18px;top:230px}
.screen--ice{left:414px;top:194px;background:var(--ice)}
.screen--night{left:805px;top:160px;background:var(--night);--line:#555;--label:var(--night-ink);--value:#9a9a9a;--circle:#151515;--circle-edge:#2c2c2c}

.topbar{position:absolute;left:0;top:0;width:100%;height:60px}
.screen--ice .topbar{background:var(--blue)}
.screen--night .topbar{background:#1a1a1a}
.menu{position:absolute;left:24px;top:19px}
.title{position:absolute;left:0;right:0;top:11px;text-align:center;font-size:32px;font-weight:300;color:#777;letter-spacing:-.5px}
.screen--ice .title,.screen--night .title{color:#fff}

.greeting{position:absolute;left:0;top:60px;width:100%;height:66px;border-top:1px solid var(--line);border-bottom:1px solid var(--line)}
.screen--night .greeting{background:var(--night-band);border-color:#3a3a3a}
.greeting .hello{position:absolute;left:22px;top:6px;font-size:15px;color:var(--blue)}
.greeting .name{position:absolute;left:20px;top:18px;font-size:38px;color:var(--blue);font-weight:400}
.greeting .split{position:absolute;left:195px;top:0;bottom:0;border-left:1px solid var(--line)}
.screen--night .greeting .split{display:none}
.score{position:absolute;left:210px;top:8px}
.score .tag{font-size:11px;color:#777}
.screen--night .score .tag{color:#ccc}
.score .big{font-size:37px;font-weight:300;color:#666;display:flex;align-items:center;gap:10px;margin-top:-3px}
.screen--night .score .big{color:#fff}
.score .delta{font-size:23px;font-weight:300}

.welcome-card{position:absolute;left:14px;top:68px;width:352px;height:57px;background:#fff;text-align:center}
.welcome-card .hello{display:block;font-size:15px;color:var(--blue);margin-top:8px}
.welcome-card .name{display:block;font-size:36px;color:var(--blue);line-height:32px}
.score--center{left:0;right:0;top:128px;text-align:center}
.score--center .big{justify-content:center;gap:8px;margin-top:-4px}

.body{position:absolute;left:0;width:100%;top:var(--tabs)}
.screen--light .body{--tabs:143px}
.screen--ice .body{--tabs:183px}
.screen--night .body{--tabs:152px}

.tabs{position:relative;height:28px;border-bottom:1px solid var(--line);margin:0 6px 0 14px}
.tab{position:absolute;top:0;height:28px;line-height:28px;text-align:center;font-size:15px;font-weight:300}
.tab--on{left:0;width:180px;border:2px solid var(--blue);border-bottom:none;background:inherit;color:var(--blue);height:29px;border-radius:2px 2px 0 0}
.screen--light .tab--on{background:#fff}
.screen--ice .tab--on{background:var(--ice)}
.screen--night .tab--on{background:var(--night)}
.tab--off{left:180px;right:0;color:#888}

.stats{position:relative;height:58px;margin-top:4px}
.chev{position:absolute;top:14px}
.chev--left{left:12px}
.chev--right{right:8px}
.stats-window{position:absolute;left:30px;right:28px;top:0;height:54px;overflow:hidden;border-left:1px solid var(--line);border-right:1px solid var(--line)}
.stat{position:absolute;top:0;white-space:nowrap}
.stat .label{font-size:15px;font-weight:500;color:var(--blue)}
.stat .value{font-size:19px;font-weight:700;color:var(--value);display:flex;align-items:center;gap:3px;margin-top:2px}
.stat--completion{left:-6px}.stat--completion .label{margin-left:11px}
.stat--sessions{left:122px}
.stat--minutes{left:230px}.stat--minutes .label{margin-left:12px}
.divider{border-top:1px solid var(--line);margin:6px 6px 0 14px}

.shortcuts{position:relative;height:80px;margin-top:10px}
.shortcut{position:absolute;top:0;width:120px;text-align:center}
.shortcut:nth-child(1){left:12px}.shortcut:nth-child(2){left:133px}.shortcut:nth-child(3){left:255px}
.dial{width:54px;height:54px;border-radius:50%;margin:0 auto;background:var(--circle);border:1px solid var(--circle-edge);
  display:flex;align-items:center;justify-content:center;font-size:21px;font-weight:300;color:var(--blue)}
.dial--active{background:var(--blue);border:3px solid #fff;box-shadow:0 0 0 1px #d5d5d5}
.screen--night .dial--active{border-color:#3a3a3a;box-shadow:none}
.shortcut .caption{font-size:10px;color:var(--label);margin-top:7px}

.next{margin-top:46px;text-align:center;font-size:19px;font-weight:300;color:#888;line-height:25px}
.screen--night .next{color:#8a8a8a;margin-top:52px}

.tabbar{position:absolute;left:0;bottom:0;width:100%;height:66px;border-top:1px solid #ddd;display:flex;background:var(--paper)}
.screen--ice .tabbar{background:#f7f7f7}
.screen--night .tabbar{background:#161616;border-color:#333}
.tabitem{flex:1;text-align:center;padding-top:10px;font-size:10px;color:#777;position:relative}
.screen--night .tabitem{color:#777}
.tabitem svg{display:block;margin:0 auto 3px}
.tabitem--on{color:var(--blue)}
.tabitem--on::before{content:"";position:absolute;left:0;right:0;top:-2px;height:3px;background:var(--blue)}
</style>
</head>
<body>

<!-- Option 1: light -->
<section class="screen screen--light">
  <header class="topbar">
    <svg class="menu" width="24" height="20" viewBox="0 0 24 20"><g fill="#555"><rect y="0" width="24" height="3.5"/><rect y="8" width="24" height="3.5"/><rect y="16" width="24" height="3.5"/></g></svg>
    <h1 class="title">Home</h1>
  </header>
  <div class="greeting">
    <span class="hello">welcome back,</span>
    <span class="name">MAYA</span>
    <span class="split"></span>
    <div class="score">
      <div class="tag">SCORE</div>
      <div class="big">650
        <svg width="16" height="22" viewBox="0 0 16 22"><path d="M5 0h6v12h5L8 22 0 12h5z" fill="var(--down)"/></svg>
        <span class="delta">-18</span></div>
    </div>
  </div>
  <div class="body">
    <div class="tabs"><span class="tab tab--on">Daily</span><span class="tab tab--off">Weekly</span></div>
    <div class="stats">
      <svg class="chev chev--left" width="12" height="22" viewBox="0 0 12 22"><path d="M10 2 2 11l8 9" stroke="var(--blue)" stroke-width="3.5" fill="none"/></svg>
      <div class="stats-window">
        <div class="stat stat--completion"><div class="label">Completion</div><div class="value">34%<svg width="10" height="14" viewBox="0 0 10 14"><path d="M3 14V6H0l5-6 5 6H7v8z" fill="var(--up)"/></svg>+4</div></div>
        <div class="stat stat--sessions"><div class="label">Sessions</div><div class="value">20 <svg width="10" height="14" viewBox="0 0 10 14"><path d="M3 14V6H0l5-6 5 6H7v8z" fill="var(--up)"/></svg>+3</div></div>
        <div class="stat stat--minutes"><div class="label">Min.</div><div class="value">18 <svg width="10" height="14" viewBox="0 0 10 14"><path d="M3 14V6H0l5-6 5 6H7v8z" fill="var(--up)"/></svg>+10</div></div>
      </div>
      <svg class="chev chev--right" width="12" height="22" viewBox="0 0 12 22"><path d="M2 2l8 9-8 9" stroke="var(--blue)" stroke-width="3.5" fill="none"/></svg>
    </div>
    <div class="divider"></div>
    <div class="shortcuts">
      <div class="shortcut"><div class="dial dial--active"><svg width="26" height="22" viewBox="0 0 26 22"><g fill="none" stroke="#fff" stroke-width="1.6"><rect x="4" y="8" width="5" height="11"/><rect x="10.5" y="2" width="5" height="17"/><rect x="17" y="10" width="5" height="9"/><path d="M1 20.5h24"/></g></svg></div><div class="caption">Analytics</div></div>
      <div class="shortcut"><div class="dial"><svg width="28" height="28" viewBox="0 0 28 28"><g fill="none" stroke="#8aa" stroke-width="1.3"><path d="M5 3h13v20H5z"/><path d="M8 8h7M8 11h7M8 14h5"/><circle cx="18" cy="16" r="4.5" stroke="var(--blue)"/><path d="M21 19.5l4 4" stroke="var(--blue)" stroke-width="2"/></g></svg></div><div class="caption">Course Overview</div></div>
      <div class="shortcut"><div class="dial">33</div><div class="caption">Days until test</div></div>
    </div>
    <p class="next">Up Next:&nbsp; Sentence Correction<br>Lesson 4</p>
  </div>
  <nav class="tabbar">
    <div class="tabitem"><svg width="34" height="26" viewBox="0 0 34 26"><g fill="none" stroke="#666" stroke-width="1.3"><path d="M2 3c5-1 10-1 15 2v19c-5-3-10-3-15-2z"/><path d="M32 3c-5-1-10-1-15 2v19c5-3 10-3 15-2z"/></g></svg>Theory</div>
    <div class="tabitem"><svg width="30" height="28" viewBox="0 0 30 28"><g fill="none" stroke="#666" stroke-width="1.2"><rect x="1" y="1" width="28" height="26"/><path d="M15 1v26M1 14h28"/></g><g font-family="Roboto,sans-serif" font-size="11" fill="#555" text-anchor="middle"><text x="8" y="11">a</text><text x="22" y="11">b</text><text x="8" y="24">c</text><text x="22" y="24">d</text></g></svg>Practice</div>
    <div class="tabitem tabitem--on"><svg width="36" height="30" viewBox="0 0 36 30"><path d="M18 1 1 15h5v14h9v-9h6v9h9V15h5z" fill="var(--blue)"/></svg>Home</div>
    <div class="tabitem"><svg width="36" height="26" viewBox="0 0 36 26"><g fill="none" stroke="#666" stroke-width="1.3"><path d="M9 5h18c5 0 8 8 8 14 0 4-4 5-7 2l-3-4H11l-3 4c-3 3-7 2-7-2C1 13 4 5 9 5z"/><path d="M10 10v6M7 13h6"/><circle cx="25" cy="11" r="1.2"/><circle cx="28" cy="14" r="1.2"/></g></svg>Games</div>
    <div class="tabitem"><svg width="30" height="28" viewBox="0 0 30 28"><g fill="none" stroke="#666" stroke-width="1.3"><path d="M4 4h16v23H4z"/><path d="M7 10h9M7 14h9M7 18h7"/><path d="M27 2l3 3-12 14-4 1 1-4z"/></g></svg>Tests</div>
  </nav>
</section>

<!-- Option 2: ice -->
<section class="screen screen--ice">
  <header class="topbar">
    <svg class="menu" width="24" height="20" viewBox="0 0 24 20"><g fill="#fff"><rect y="0" width="24" height="3.5"/><rect y="8" width="24" height="3.5"/><rect y="16" width="24" height="3.5"/></g></svg>
    <h1 class="title">Home</h1>
  </header>
  <div class="welcome-card"><span class="hello">Welcome back,</span><span class="name">MAYA</span></div>
  <div class="score score--center">
    <div class="tag">SCORE</div>
    <div class="big">650
      <svg width="16" height="22" viewBox="0 0 16 22"><path d="M5 0h6v12h5L8 22 0 12h5z" fill="var(--down)"/></svg>
      <span class="delta">-18</span></div>
  </div>
  <div class="body">
    <div class="tabs"><span class="tab tab--on">Daily</span><span class="tab tab--off">Weekly</span></div>
    <div class="stats">
      <svg class="chev chev--left" width="12" height="22" viewBox="0 0 12 22"><path d="M10 2 2 11l8 9" stroke="var(--blue)" stroke-width="3.5" fill="none"/></svg>
      <div class="stats-window">
        <div class="stat stat--completion"><div class="label">Completion</div><div class="value">34%<svg width="10" height="14" viewBox="0 0 10 14"><path d="M3 14V6H0l5-6 5 6H7v8z" fill="var(--up)"/></svg>+4</div></div>
        <div class="stat stat--sessions"><div class="label">Sessions</div><div class="value">20 <svg width="10" height="14" viewBox="0 0 10 14"><path d="M3 14V6H0l5-6 5 6H7v8z" fill="var(--up)"/></svg>+3</div></div>
        <div class="stat stat--minutes"><div class="label">Min.</div><div class="value">18 <svg width="10" height="14" viewBox="0 0 10 14"><path d="M3 14V6H0l5-6 5 6H7v8z" fill="var(--up)"/></svg>+10</div></div>
      </div>
      <svg class="chev chev--right" width="12" height="22" viewBox="0 0 12 22"><path d="M2 2l8 9-8 9" stroke="var(--blue)" stroke-width="3.5" fill="none"/></svg>
    </div>
    <div class="divider"></div>
    <div class="shortcuts">
      <div class="shortcut"><div class="dial dial--active"><svg width="26" height="22" viewBox="0 0 26 22"><g fill="none" stroke="#fff" stroke-width="1.6"><rect x="4" y="8" width="5" height="11"/><rect x="10.5" y="2" width="5" height="17"/><rect x="17" y="10" width="5" height="9"/><path d="M1 20.5h24"/></g></svg></div><div class="caption">Analytics</div></div>
      <div class="shortcut"><div class="dial"><svg width="28" height="28" viewBox="0 0 28 28"><g fill="none" stroke="#8aa" stroke-width="1.3"><path d="M5 3h13v20H5z"/><path d="M8 8h7M8 11h7M8 14h5"/><circle cx="18" cy="16" r="4.5" stroke="var(--blue)"/><path d="M21 19.5l4 4" stroke="var(--blue)" stroke-width="2"/></g></svg></div><div class="caption">Course Overview</div></div>
      <div class="shortcut"><div class="dial">33</div><div class="caption">Days until test</div></div>
    </div>
    <p class="next">Up Next:&nbsp; Sentence Correction<br>Lesson 4</p>
  </div>
  <nav class="tabbar">
    <div class="tabitem"><svg width="34" height="26" viewBox="0 0 34 26"><g fill="none" stroke="#666" stroke-width="1.3"><path d="M2 3c5-1 10-1 15 2v19c-5-3-10-3-15-2z"/><path d="M32 3c-5-1-10-1-15 2v19c5-3 10-3 15-2z"/></g></svg>Theory</div>
    <div class="tabitem"><svg width="30" height="28" viewBox="0 0 30 28"><g fill="none" stroke="#666" stroke-width="1.2"><rect x="1" y="1" width="28" height="26"/><path d="M15 1v26M1 14h28"/></g><g font-family="Roboto,sans-serif" font-size="11" fill="#555" text-anchor="middle"><text x="8" y="11">a</text><text x="22" y="11">b</text><text x="8" y="24">c</text><text x="22" y="24">d</text></g></svg>Practice</div>
    <div class="tabitem tabitem--on"><svg width="36" height="30" viewBox="0 0 36 30"><path d="M18 1 1 15h5v14h9v-9h6v9h9V15h5z" fill="var(--blue)"/></svg>Home</div>
    <div class="tabitem"><svg width="36" height="26" viewBox="0 0 36 26"><g fill="none" stroke="#666" stroke-width="1.3"><path d="M9 5h18c5 0 8 8 8 14 0 4-4 5-7 2l-3-4H11l-3 4c-3 3-7 2-7-2C1 13 4 5 9 5z"/><path d="M10 10v6M7 13h6"/><circle cx="25" cy="11" r="1.2"/><circle cx="28" cy="14" r="1.2"/></g></svg>Games</div>
    <div class="tabitem"><svg width="30" height="28" viewBox="0 0 30 28"><g fill="none" stroke="#666" stroke-width="1.3"><path d="M4 4h16v23H4z"/><path d="M7 10h9M7 14h9M7 18h7"/><path d="M27 2l3 3-12 14-4 1 1-4z"/></g></svg>Tests</div>
  </nav>
</section>

<!-- Option 3: night -->
<section class="screen screen--night">
  <header class="topbar">
    <svg class="menu" width="24" height="20" viewBox="0 0 24 20"><g fill="#fff"><rect y="0" width="24" height="3.5"/><rect y="8" width="24" height="3.5"/><rect y="16" width="24" height="3.5"/></g></svg>
    <h1 class="title">Home</h1>
  </header>
  <div class="greeting">
    <span class="hello">welcome back,</span>
    <span class="name">MAYA</span>
    <span class="split"></span>
    <div class="score" style="left:225px">
      <div class="tag">SCORE</div>
      <div class="big">650
        <svg width="16" height="22" viewBox="0 0 16 22"><path d="M5 0h6v12h5L8 22 0 12h5z" fill="var(--down)"/></svg>
        <span class="delta">-18</span></div>
    </div>
  </div>
  <div class="body">
    <div class="tabs"><span class="tab tab--on">Daily</span><span class="tab tab--off">Weekly</span></div>
    <div class="stats">
      <svg class="chev chev--left" width="12" height="22" viewBox="0 0 12 22"><path d="M10 2 2 11l8 9" stroke="var(--blue)" stroke-width="3.5" fill="none"/></svg>
      <div class="stats-window">
        <div class="stat stat--completion"><div class="label">Completion</div><div class="value">34%<svg width="10" height="14" viewBox="0 0 10 14"><path d="M3 14V6H0l5-6 5 6H7v8z" fill="var(--up)"/></svg>+4</div></div>
        <div class="stat stat--sessions"><div class="label">Sessions</div><div class="value">20 <svg width="10" height="14" viewBox="0 0 10 14"><path d="M3 14V6H0l5-6 5 6H7v8z" fill="var(--up)"/></svg>+3</div></div>
        <div class="stat stat--minutes"><div class="label">Min.</div><div class="value">18 <svg width="10" height="14" viewBox="0 0 10 14"><path d="M3 14V6H0l5-6 5 6H7v8z" fill="var(--up)"/></svg>+10</div></div>
      </div>
      <svg class="chev chev--right" width="12" height="22" viewBox="0 0 12 22"><path d="M2 2l8 9-8 9" stroke="var(--blue)" stroke-width="3.5" fill="none"/></svg>
    </div>
    <div class="divider"></div>
    <div class="shortcuts">
      <div class="shortcut"><div class="dial dial--active"><svg width="26" height="22" viewBox="0 0 26 22"><g fill="none" stroke="#fff" stroke-width="1.6"><rect x="4" y="8" width="5" height="11"/><rect x="10.5" y="2" width="5" height="17"/><rect x="17" y="10" width="5" height="9"/><path d="M1 20.5h24"/></g></svg></div><div class="caption">Analytics</div></div>
      <div class="shortcut"><div class="dial"><svg width="28" height="28" viewBox="0 0 28 28"><g fill="none" stroke="#6a8088" stroke-width="1.3"><path d="M5 3h13v20H5z"/><path d="M8 8h7M8 11h7M8 14h5"/><circle cx="18" cy="16" r="4.5" stroke="var(--blue)"/><path d="M21 19.5l4 4" stroke="var(--blue)" stroke-width="2"/></g></svg></div><div class="caption">Course Overview</div></div>
      <div class="shortcut"><div class="dial">33</div><div class="caption">Days until test</div></div>
    </div>
    <p class="next">Up Next:&nbsp; Sentence Correction<br>Lesson 4</p>
  </div>
  <nav class="tabbar">
    <div class="tabitem"><svg width="34" height="26" viewBox="0 0 34 26"><g fill="none" stroke="#777" stroke-width="1.3"><path d="M2 3c5-1 10-1 15 2v19c-5-3-10-3-15-2z"/><path d="M32 3c-5-1-10-1-15 2v19c5-3 10-3 15-2z"/></g></svg>Theory</div>
    <div class="tabitem"><svg width="30" height="28" viewBox="0 0 30 28"><g fill="none" stroke="#777" stroke-width="1.2"><rect x="1" y="1" width="28" height="26"/><path d="M15 1v26M1 14h28"/></g><g font-family="Roboto,sans-serif" font-size="11" fill="#888" text-anchor="middle"><text x="8" y="11">a</text><text x="22" y="11">b</text><text x="8" y="24">c</text><text x="22" y="24">d</text></g></svg>Practice</div>
    <div class="tabitem tabitem--on"><svg width="36" height="30" viewBox="0 0 36 30"><path d="M18 1 1 15h5v14h9v-9h6v9h9V15h5z" fill="var(--blue)"/></svg>Home</div>
    <div class="tabitem"><svg width="36" height="26" viewBox="0 0 36 26"><g fill="none" stroke="#777" stroke-width="1.3"><path d="M9 5h18c5 0 8 8 8 14 0 4-4 5-7 2l-3-4H11l-3 4c-3 3-7 2-7-2C1 13 4 5 9 5z"/><path d="M10 10v6M7 13h6"/><circle cx="25" cy="11" r="1.2"/><circle cx="28" cy="14" r="1.2"/></g></svg>Games</div>
    <div class="tabitem"><svg width="30" height="28" viewBox="0 0 30 28"><g fill="none" stroke="#777" stroke-width="1.3"><path d="M4 4h16v23H4z"/><path d="M7 10h9M7 14h9M7 18h7"/><path d="M27 2l3 3-12 14-4 1 1-4z"/></g></svg>Tests</div>
  </nav>
</section>

</body>
</html>
```